Vantro cards

I am in the auto motive, transportation business I would like a business card that is Something cool, modern edgy, having to do with car culture. I offer towing service for high and exotic cars. I also provide towing for collisions and car accidents. I offer open and enclosed transport nationwide.

Target Market(s)

Car culture people high end auto collectors

Industry/Entity Type

Towing car carrier

Contact Information for Business Card

My company colors black yellow and silver

Font styles to use
Serif

```html
<!DOCTYPE html>
<html lang="en">
<head>
<meta charset="utf-8">
<title>Vantro Business Cards</title>
<link rel="stylesheet" href="https://fonts.googleapis.com/css2?family=Domine:wght@400;700&family=Lato:wght@400;700&display=swap">
<style>
  :root {
    --backdrop: #2b2b2d;
    --card: #1f1f20;
    --card-back: #1c1c1d;
    --yellow: #f2d23c;
    --white: #f4f4f2;
    --silver: #c9c9c9;
    --emboss: #0e0e0f;
  }
  * { margin: 0; padding: 0; box-sizing: border-box; }
  html, body {
    width: 1200px;
    height: 800px;
    overflow: hidden;
    background: var(--backdrop);
  }
  .stage {
    width: 1200px;
    height: 800px;
    display: flex;
    align-items: center;
    justify-content: center;
    gap: 50px;
  }
  .card {
    position: relative;
    width: 540px;
    height: 310px;
    border-radius: 18px;
    background: var(--card);
    border-bottom: 4px solid var(--yellow);
    box-shadow: 0 14px 30px rgba(0,0,0,0.45);
    overflow: hidden;
  }
  .card--back { background: var(--card-back); }

  .brand-mark {
    position: absolute;
    display: flex;
    align-items: center;
    gap: 10px;
    font-family: "Domine", serif;
    font-weight: 700;
    letter-spacing: 1px;
    text-transform: uppercase;
  }
  .brand-mark__square {
    width: 14px;
    height: 14px;
    background: currentColor;
  }
  .card--front .brand-mark {
    left: 44px;
    top: 128px;
    font-size: 36px;
    color: var(--yellow);
  }
  .card--back .brand-mark {
    left: 0;
    right: 0;
    top: 120px;
    justify-content: center;
    font-size: 58px;
    color: var(--emboss);
    letter-spacing: 3px;
  }

  .contact-block {
    position: absolute;
    left: 300px;
    top: 84px;
    width: 220px;
  }
  .contact-block__name {
    font-family: "Domine", serif;
    font-weight: 400;
    font-size: 21px;
    letter-spacing: 1px;
    color: var(--yellow);
    text-transform: uppercase;
    white-space: nowrap;
  }
  .contact-block__title {
    font-family: "Lato", sans-serif;
    font-size: 14px;
    color: var(--white);
    margin-top: 2px;
  }
  .contact-block__rule {
    width: 90px;
    height: 2px;
    background: var(--yellow);
    margin: 12px 0 14px;
  }
  .contact-list { list-style: none; }
  .contact-list__item {
    display: flex;
    align-items: center;
    gap: 9px;
    font-family: "Lato", sans-serif;
    font-size: 12px;
    color: var(--white);
    line-height: 1;
    margin-bottom: 8px;
    white-space: nowrap;
  }
  .contact-list__item--phone { font-size: 15px; }
  .contact-icon { width: 12px; height: 12px; flex: none; }
</style>
</head>
<body>
<main class="stage">
  <section class="card card--front" aria-label="Business card front">
    <div class="brand-mark"><span class="brand-mark__square"></span>Vantro</div>
    <div class="contact-block">
      <h1 class="contact-block__name">Daniel Corvell</h1>
      <p class="contact-block__title">Managing Director</p>
      <div class="contact-block__rule"></div>
      <ul class="contact-list">
        <li class="contact-list__item contact-list__item--phone">
          <svg class="contact-icon" viewBox="0 0 12 12" aria-hidden="true">
            <path d="M2.5 1 L4.5 1 L5.2 3.6 L4 4.6 Q5 7 7.4 8 L8.4 6.8 L11 7.5 L11 9.5 Q11 11 9.5 11 Q1 10 1 2.5 Q1 1 2.5 1 Z" fill="#f2d23c"/>
          </svg>
          555-204-7316
        </li>
        <li class="contact-list__item">
          <svg class="contact-icon" viewBox="0 0 12 12" aria-hidden="true">
            <rect x="0.5" y="2.5" width="11" height="7.5" fill="#f2d23c"/>
            <path d="M0.5 2.5 L6 7 L11.5 2.5" fill="none" stroke="#1f1f20" stroke-width="1"/>
          </svg>
          corvell@vantrohaul.com
        </li>
        <li class="contact-list__item">
          <svg class="contact-icon" viewBox="0 0 12 12" aria-hidden="true">
            <circle cx="6" cy="6" r="5.5" fill="#f2d23c"/>
            <path d="M0.5 6 H11.5 M6 0.5 Q2.5 6 6 11.5 M6 0.5 Q9.5 6 6 11.5" fill="none" stroke="#1f1f20" stroke-width="0.8"/>
          </svg>
          www.vantrohaul.com
        </li>
      </ul>
    </div>
  </section>

  <section class="card card--back" aria-label="Business card back">
    <div class="brand-mark"><span class="brand-mark__square"></span>Vantro</div>
  </section>
</main>
</body>
</html>
```